Brell Stone Company Business Cards

Front and Back Business Card - logo and text setup - cool design. I need workable photoshop or illustrator files so I can setup each employee card with design that is created
Updates

Hi everyone, thank you for the great entries. Please no more white and blue cards - there are so many already - black and silver only now please. thanks!

Target Market(s)

Construction Industry - Facility Managers

Industry/Entity Type

Construction

Contact Information for Business Card

I really like contemporary simplistic looks - clean neat....not opposed to seeing some black backrounds

Requirements
Must have
• Logo/website address with design on front only - www.brellstone-example.com (logo attached)
• Back:
• Name/Title/Company Address/Phone/email address
Nice to have
• Cool design
Should not have
• Nothing gimmicky like Fire or Water - since we are a Fire Protection company - it has all been done

```html
<!DOCTYPE html>
<html lang="en">
<head>
<meta charset="utf-8">
<title>Brell Stone Company Business Cards</title>
<link rel="stylesheet" href="https://fonts.googleapis.com/css2?family=Poppins:wght@400;500;600;700&display=swap">
<style>
  :root {
    --black: #141414;
    --black-soft: #262626;
    --silver: #a9adb2;
    --silver-light: #c9ccd0;
    --ink: #161616;
    --grey-text: #5a5d62;
    --paper: #f5f5f5;
    --backdrop: #e6e6e6;
  }
  * { margin: 0; padding: 0; box-sizing: border-box; }
  html, body {
    width: 1200px; height: 920px; overflow: hidden;
    background: var(--backdrop);
    font-family: "Poppins", sans-serif;
  }
  .canvas { position: relative; width: 1200px; height: 920px; }

  .card {
    position: absolute; top: 310px;
    width: 540px; height: 300px;
    box-shadow: 0 6px 16px rgba(0,0,0,0.22);
    overflow: hidden;
  }

  /* Front */
  .card-front { left: 40px; background: var(--black); }
  .card-front .wordmark {
    position: absolute; left: 0; right: 0; top: 100px;
    text-align: center;
    font-size: 62px; font-weight: 700; letter-spacing: -1px;
    color: var(--black-soft);
  }
  .card-front .website {
    position: absolute; left: 0; right: 0; top: 256px;
    text-align: center;
    font-size: 13px; letter-spacing: 1px; color: #ffffff;
  }
  .card-front .website .name { color: var(--silver); }

  /* Back */
  .card-back { left: 620px; background: var(--paper); }
  .card-back .wordmark {
    position: absolute; right: 34px; top: 26px;
    font-size: 54px; font-weight: 700; letter-spacing: -1px;
    color: var(--ink);
  }
  .card-back .side-tab {
    position: absolute; left: 0; top: 139px; width: 7px; height: 36px;
    background: var(--black);
  }
  .card-back .person-name {
    position: absolute; left: 38px; top: 136px;
    font-size: 18px; font-weight: 600; color: var(--ink); letter-spacing: 0.3px;
  }
  .card-back .person-title {
    position: absolute; left: 38px; top: 164px;
    font-size: 12px; color: var(--grey-text);
  }
  .card-back .divider {
    position: absolute; left: 38px; right: 34px; top: 196px;
    height: 1px; background: var(--silver);
  }
  .contact-list {
    position: absolute; left: 38px; top: 208px; list-style: none;
  }
  .contact-list li {
    display: flex; align-items: center; gap: 8px;
    height: 22px; font-size: 13px; color: #2b2d31;
  }
  .contact-list svg { width: 14px; height: 14px; }
  .address {
    position: absolute; right: 34px; top: 230px;
    text-align: right; font-size: 12.5px; line-height: 22px; color: var(--grey-text);
  }
  .bottom-band {
    position: absolute; left: 0; right: 0; bottom: 0; height: 8px; display: flex;
  }
  .bottom-band .dark { width: 335px; background: var(--black); }
  .bottom-band .gap { width: 4px; background: var(--paper); }
  .bottom-band .light { flex: 1; background: var(--silver); }
</style>
</head>
<body>
<main class="canvas">

  <section class="card card-front" aria-label="Card front">
    <div class="wordmark">brellstone</div>
    <div class="website">www.<span class="name">brellstone-example</span>.com</div>
  </section>

  <section class="card card-back" aria-label="Card back">
    <div class="wordmark">brellstone</div>
    <div class="side-tab"></div>
    <div class="person-name">DANA WHITFIELD</div>
    <div class="person-title">Director</div>
    <div class="divider"></div>

    <ul class="contact-list">
      <li>
        <svg viewBox="0 0 14 14" aria-hidden="true">
          <circle cx="7" cy="7" r="6.2" fill="none" stroke="#a9adb2" stroke-width="1.2"/>
          <path d="M4.6 3.8 L5.8 3.6 L6.4 5.2 L5.6 5.9 Q6.3 7.6 8 8.4 L8.7 7.6 L10.3 8.2 L10.1 9.4 Q7.6 10.2 5.4 8.1 Q3.6 6 4.6 3.8 Z" fill="#141414"/>
        </svg>
        (555) 014-2290
      </li>
      <li>
        <svg viewBox="0 0 14 14" aria-hidden="true">
          <circle cx="7" cy="7" r="6.2" fill="none" stroke="#a9adb2" stroke-width="1.2"/>
          <rect x="3.6" y="4.6" width="6.8" height="4.8" fill="none" stroke="#141414" stroke-width="1"/>
          <path d="M3.6 4.6 L7 7.4 L10.4 4.6" fill="none" stroke="#141414" stroke-width="1"/>
        </svg>
        info@brellstone-example.com
      </li>
      <li>
        <svg viewBox="0 0 14 14" aria-hidden="true">
          <circle cx="7" cy="7" r="6.2" fill="none" stroke="#a9adb2" stroke-width="1.2"/>
          <circle cx="7" cy="7" r="3.4" fill="none" stroke="#141414" stroke-width="1"/>
          <path d="M3.6 7 H10.4 M7 3.6 Q5.2 7 7 10.4 M7 3.6 Q8.8 7 7 10.4" fill="none" stroke="#141414" stroke-width="0.8"/>
        </svg>
        www.brellstone-example.com
      </li>
    </ul>

    <div class="address">
      48 Harbor Point Road<br>
      Port Alden, NY 10990
    </div>

    <div class="bottom-band"><span class="dark"></span><span class="gap"></span><span class="light"></span></div>
  </section>

</main>
</body>
</html>
```